Hollow Mesa Farm Vault Reserve Wine Label (Front and Back)

I need to create an elite tier wine label.  I would like it to be in a light, natural color with silver or gold.  I would like it to look rich and expensive, mostly monochromatic, elegantly simple.  It will need to stand up next to wine labels that are black and charcoal colored and look like the more expensive wine of the 3.  I have attached a similar label that it will be grouped with and some instructions.
We are a winery in southeast Washington state with a reputation for fine wines and top notch terroir.  We want to present family, tradition and high value wine in the bottle.

```html
<!DOCTYPE html>
<html lang="en">
<head>
<meta charset="utf-8">
<title>Hollow Mesa Farm – Vault Reserve Cabernet Sauvignon Labels</title>
<link rel="stylesheet" href="https://fonts.googleapis.com/css2?family=Marcellus&family=Cinzel:wght@700&family=Open+Sans:wght@400;700&display=swap">
<style>
  :root {
    --backdrop: #e6e8e9;
    --linen: #ece5d6;
    --linen-deep: #ddd2bc;
    --ivory: #f7f3ea;
    --sand: #d3c5a8;
    --ink: #5a4c3a;
    --ink-soft: #7a6a55;
    --gold-light: #ecd29a;
    --gold: #c9a15b;
    --gold-dark: #9a7536;
  }
  * { box-sizing: border-box; margin: 0; padding: 0; }
  html, body { width: 1200px; height: 1000px; overflow: hidden; }
  body { background: var(--backdrop); position: relative; font-family: "Open Sans", sans-serif; }

  .label { position: absolute; overflow: hidden; box-shadow: 0 8px 24px rgba(0,0,0,.14); }
  .label-texture { position: absolute; inset: 0; background: linear-gradient(160deg, var(--linen), var(--linen-deep)); }
  .abs { position: absolute; }
  .gold-stripe { position: absolute; left: 0; right: 0; background: linear-gradient(90deg, var(--gold-dark), var(--gold-light) 35%, var(--gold) 65%, var(--gold-light)); }

  /* Front label */
  .front { left: 170px; top: 150px; width: 400px; height: 700px; }
  .front .lower-field { position: absolute; left: 0; right: 0; top: 330px; height: 160px; background: var(--sand); opacity: .55; }
  .cartouche { position: absolute; inset: 0; }
  .brand-mark { left: 0; right: 0; top: 111px; display: flex; justify-content: center; align-items: center; gap: 5px; font-family: "Marcellus", serif; font-size: 9px; letter-spacing: .5px; color: var(--ink); text-transform: uppercase; }
  .brand-mark .mark-square { width: 11px; height: 11px; border: 1.5px solid var(--gold-dark); }
  .mark-rule { top: 117px; height: 1.5px; width: 24px; background: var(--gold); }
  .wordmark-main { left: 0; right: 0; top: 142px; text-align: center; font-family: "Marcellus", serif; font-size: 54px; line-height: 1; color: var(--ink); letter-spacing: 1px; }
  .wordmark-sub { left: 0; right: 0; top: 206px; text-align: center; font-family: "Marcellus", serif; font-size: 21px; color: var(--ink); letter-spacing: 1.5px; }
  .wordmark-rule { left: 130px; width: 140px; top: 246px; height: 2px; background: linear-gradient(90deg, transparent, var(--gold), transparent); }
  .appellation { left: 0; right: 0; top: 261px; text-align: center; font-weight: 700; font-size: 13px; letter-spacing: 1.5px; color: var(--ink-soft); }
  .vineyard { left: 0; right: 0; top: 372px; text-align: center; font-weight: 700; font-size: 13px; letter-spacing: 1.8px; color: var(--ink); }
  .vintage { left: 0; right: 0; top: 394px; text-align: center; font-family: "Marcellus", serif; font-size: 22px; letter-spacing: 2px; color: var(--ink); }
  .tier-band { left: 0; right: 0; top: 500px; height: 48px; background: var(--sand); display: flex; align-items: center; justify-content: center; font-family: "Marcellus", serif; font-size: 20px; letter-spacing: 1.5px; color: var(--ink); }
  .varietal-band { left: 0; right: 0; top: 552px; height: 58px; background: var(--ivory); display: flex; align-items: center; justify-content: center; font-family: "Marcellus", serif; font-size: 24px; letter-spacing: 1px; color: var(--ink); }
  .heritage-line { left: 0; right: 0; top: 641px; text-align: center; font-family: "Marcellus", serif; font-size: 9.5px; letter-spacing: .6px; color: var(--ink); }
  .heritage-line .count { font-size: 17px; vertical-align: -2px; margin: 0 2px; }

  /* Back label */
  .back { left: 640px; top: 240px; width: 400px; height: 540px; }
  .back-header { left: 0; right: 0; top: 44px; height: 46px; background: var(--ivory); padding-left: 30px; display: flex; align-items: center; font-family: "Cinzel", serif; font-weight: 700; font-size: 17px; letter-spacing: 1px; color: var(--ink); }
  .back-badge { right: 18px; top: 30px; }
  .story { left: 30px; right: 30px; top: 125px; text-align: center; font-size: 10.5px; line-height: 1.55; color: var(--ink); }
  .signature { width: 110px; height: 22px; background: linear-gradient(90deg, rgba(154,117,54,.12), rgba(154,117,54,.3), rgba(154,117,54,.12)); border-radius: 3px; }
  .signer { top: 290px; display: flex; flex-direction: column; align-items: center; gap: 5px; font-size: 8.5px; color: var(--ink); }
  .signer-left { left: 30px; }
  .signer-right { right: 30px; top: 300px; }
  .warning { left: 30px; right: 30px; top: 345px; font-size: 8.5px; line-height: 1.45; color: var(--ink); }
  .warning strong { font-weight: 700; }
  .facts { left: 30px; top: 410px; font-size: 8.5px; line-height: 1.45; color: var(--ink); text-transform: uppercase; }
  .facts strong { display: block; font-weight: 700; }
  .facts .gap { height: 10px; }
  .volume { left: 200px; top: 420px; padding: 2px 6px; background: var(--ivory); border: 1px solid var(--gold); color: var(--ink); font-weight: 700; font-size: 13px; border-radius: 2px; }
  .seal { left: 208px; top: 460px; width: 36px; height: 36px; border-radius: 50%; border: 2px solid var(--gold); }
</style>
</head>
<body>

<section class="label front" aria-label="Front label">
  <div class="label-texture" role="img" aria-label="Linen damask pattern background"></div>
  <div class="lower-field" role="img" aria-label="Soft sand damask pattern field"></div>

  <svg class="cartouche" viewBox="0 0 400 700" width="400" height="700" aria-hidden="true">
    <defs>
      <linearGradient id="goldEdge" x1="0" y1="0" x2="1" y2="1">
        <stop offset="0" stop-color="#ecd29a"/>
        <stop offset=".45" stop-color="#c9a15b"/>
        <stop offset=".7" stop-color="#ecd29a"/>
        <stop offset="1" stop-color="#9a7536"/>
      </linearGradient>
    </defs>
    <path d="M200 62 C228 82 252 92 288 90 C300 112 320 122 344 122 L344 398 C320 410 302 430 292 462 L242 462 C226 472 212 484 200 506 C188 484 174 472 158 462 L108 462 C98 430 80 410 56 398 L56 122 C80 122 100 112 112 90 C148 92 172 82 200 62 Z"
          fill="#f7f3ea" stroke="url(#goldEdge)" stroke-width="8"/>
    <path d="M72 356 H328 V398 C308 410 296 425 288 446 L238 446 C222 456 210 466 200 484 C190 466 178 456 162 446 L112 446 C104 425 92 410 72 398 Z"
          fill="#e3d7bf"/>
  </svg>

  <div class="abs mark-rule" style="left:110px"></div>
  <div class="abs mark-rule" style="right:110px"></div>
  <div class="abs brand-mark"><span class="mark-square"></span>Hollow Mesa Farm</div>
  <div class="abs wordmark-main">HOLLOW</div>
  <div class="abs wordmark-sub">MESA FARM</div>
  <div class="abs wordmark-rule"></div>
  <div class="abs appellation">HORSE HEAVEN HILLS</div>
  <div class="abs vineyard">ESTATE VINEYARD</div>
  <div class="abs vintage">2022</div>

  <div class="abs tier-band">VAULT RESERVE</div>
  <div class="abs varietal-band">CABERNET SAUVIGNON</div>
  <div class="gold-stripe" style="top:618px;height:8px"></div>
  <div class="abs heritage-line">FAMILY STEWARDS OF THE LAND FOR <span class="count">5</span> GENERATIONS</div>
  <div class="gold-stripe" style="top:670px;height:10px"></div>
</section>

<section class="label back" aria-label="Back label">
  <div class="label-texture" role="img" aria-label="Linen damask pattern background"></div>
  <div class="abs back-header">HOLLOW MESA FARM</div>
  <div class="gold-stripe" style="top:94px;height:4px"></div>
  <svg class="abs back-badge" width="56" height="76" viewBox="0 0 56 76" aria-hidden="true">
    <path d="M28 2 C36 8 44 10 54 10 V58 C44 62 36 66 28 74 C20 66 12 62 2 58 V10 C12 10 20 8 28 2 Z" fill="#f7f3ea" stroke="#c9a15b" stroke-width="3"/>
  </svg>

  <p class="abs story">"Hollow Mesa Farm wines are exclusively sourced from our family's Estate Vineyard in the Horse Heaven Hills of Washington state. For five generations, we have cultivated this rugged and fertile land, embodying our deep-seated love and dedication. We believe that exceptional wine is the result of outstanding vineyards, limited production, and astute winemaking. With the utmost pride and joy, we present this exquisite Cabernet Sauvignon from our ranch to your table." Cheers,</p>

  <div class="abs signer signer-left">
    <div class="signature" role="img" aria-label="Handwritten signature of Maren Hollis"></div>
    <span>Maren Hollis, Winemaker</span>
  </div>
  <div class="abs signer signer-right">
    <div class="signature" role="img" aria-label="Handwritten signature of Dale Orrin"></div>
    <span>Dale Orrin, Farmer &amp; Proprietor</span>
  </div>

  <p class="abs warning"><strong>GOVERNMENT WARNING:</strong> (1) According to the Surgeon General, women should not drink alcoholic beverages during pregnancy because of the risk of birth defects. (2) Consumption of alcoholic beverages impairs your ability to drive a car or operate machinery, and may cause health problems.</p>

  <div class="abs facts">
    <strong>Contains Sulfites</strong>
    15% Alc. by Vol.
    <div class="gap"></div>
    <strong>Produced and Bottled</strong>
    by Orrin Wine Estates, LLC,<br>
    Sagebrush Flat WA, USA
  </div>
  <div class="abs volume">750ml</div>
  <div class="abs seal" aria-hidden="true"></div>

  <div class="gold-stripe" style="top:518px;height:9px"></div>
</section>

</body>
</html>
```